Front and back cover design for skincare marketing materials

Thank you for showing an interest in my project.
Project Details.

I require a front and back cover for our marketing materials.
·       Front Cover size: 105 mm W x 150 mm H.
·       Back Cover size:  105 mm W x 150 mm H.
·       It must include these two colors. You can use a third color if you wish.
1.     #DBA09D
2.     #FFFFFF
 
Front Cover
·      The front cover will have a faded image of the Kakadu Plum branch and fruit. There are two image files, KP_image-1.jpg and kp_image-2.jpeg. You can use both images, just a portion of them, or source alternative royalty-free images of Kakadu Plum that may better fit the design. These two files have been uploaded.
 
The front cover wording.
Top of the front cover.
a.     The title of the image. “Kakadu Plum”
b.     The brand name, “Vellora Skincare”. The file brand_name.ai uploaded.
 
Bottom of the front cover- Designer's choice of font.
The bottom of the front cover contains three lines of text in the following order.  
1.     Australian Native Ingredients
2.     100% Natural · Organic · Wild-harvested
3.     Australian-Made Premium Skincare
 
Back Cover
·      Back Cover wording.The back cover contains the following words "grown by nature" in white (#FFFFFF) of font Italianno (font_file.ttf) with a background color of #DBA09D as seen in the sample box (sample_box.pdf) right-side panel
 
Please provide one file for the front cover and a separate file for the back cover.
All the elements of the files must be editable.
 
Do NOT use the Curve function on the files, as the text must remain editable/changeable.
 
All assets/resources/files, including fonts not supplied by us but used by the designer, must be named and provided with the finished design.
Updates

Slow to provide project details.

Target Market(s)

Beauty-minded Asian consumers between the ages of 32 and 75 who take a proactive approach to maintaining younger-looking skin. Those who already know the danger of skin damage caused by skincare containing harsh chemicals choose effective natural/organic solutions to meet their skincare needs. Those who wish a more radiant glow and youthful appearance to their skin. Usually, a two-income middle to high-income bracket couples with a mindset for health and beauty.

Industry/Entity Type

beauty

Font styles to use
Other font styles liked:
• I will provide a font file and a brand name file.

Requirements
Must have
• You must use the two colors provided on the product box. The designer may use a third color.
Nice to have
• some gold colour

```html
<!DOCTYPE html>
<html lang="en">
<head>
<meta charset="utf-8">
<title>Vellora Skincare – Kakadu Plum covers</title>
<link rel="stylesheet" href="https://fonts.googleapis.com/css2?family=Italianno&family=Montserrat:wght@400&display=swap">
<style>
  :root {
    --rose: #DBA09D;
    --white: #FFFFFF;
    --slate: #545a5f;
    --leaf-light: #c9d86a;
    --leaf-mid: #8fae3c;
    --leaf-deep: #4f7a2a;
    --shadow: rgba(0, 0, 0, 0.35);
  }
  html, body {
    margin: 0;
    padding: 0;
    width: 1200px;
    height: 960px;
    overflow: hidden;
    background: var(--white);
  }
  .canvas {
    position: relative;
    width: 1200px;
    height: 960px;
  }
  .cover {
    position: absolute;
    top: 142px;
    width: 476px;
    height: 680px;
    background: var(--rose);
    box-shadow: 8px 8px 6px var(--shadow);
  }
  .cover--back { left: 98px; }
  .cover--front { left: 620px; }

  .tagline {
    position: absolute;
    left: 0;
    right: 0;
    top: 288px;
    margin: 0;
    text-align: center;
    font-family: "Italianno", cursive;
    font-weight: 400;
    font-size: 72px;
    line-height: 1;
    color: var(--white);
    transform: translateX(-4px);
  }

  .brand-name {
    position: absolute;
    left: 0;
    right: 0;
    top: 36px;
    margin: 0;
    text-align: center;
    font-family: "Italianno", cursive;
    font-weight: 400;
    font-size: 64px;
    line-height: 1;
    color: var(--white);
  }

  .fruit-photo {
    position: absolute;
    left: 106px;
    top: 138px;
    width: 274px;
    height: 277px;
    border-radius: 50%;
    background: radial-gradient(circle at 40% 40%, var(--leaf-light) 0%, var(--leaf-mid) 55%, var(--leaf-deep) 100%);
  }

  .product-title {
    position: absolute;
    left: 0;
    right: 0;
    top: 448px;
    margin: 0;
    text-align: center;
    font-weight: 400;
  }
  .product-title__script {
    display: block;
    font-family: "Italianno", cursive;
    font-weight: 400;
    font-size: 140px;
    line-height: 0.75;
    color: var(--white);
    transform: translateX(4px);
  }
  .product-title__caps {
    display: block;
    margin-top: -22px;
    font-family: "Montserrat", sans-serif;
    font-weight: 400;
    font-size: 40px;
    letter-spacing: 18px;
    padding-left: 18px;
    line-height: 1;
    color: var(--slate);
  }

  .claims {
    position: absolute;
    left: 0;
    top: 590px;
    width: 476px;
    height: 56px;
  }
</style>
</head>
<body>
<main class="canvas">
  <section class="cover cover--back" aria-label="Back cover">
    <p class="tagline">grown by nature</p>
  </section>

  <section class="cover cover--front" aria-label="Front cover">
    <h2 class="brand-name">Vellora Skincare</h2>
    <div class="fruit-photo" role="img" aria-label="Photograph of Kakadu plum fruit hanging on a leafy branch"></div>
    <h1 class="product-title">
      <span class="product-title__script">Kakadu</span>
      <span class="product-title__caps">PLUM</span>
    </h1>
    <svg class="claims" viewBox="0 0 476 56" aria-label="Product claim badges">
      <circle cx="158" cy="28" r="26" fill="none" stroke="var(--white)" stroke-width="1.2"/>
      <circle cx="240" cy="28" r="26" fill="none" stroke="var(--white)" stroke-width="1.2"/>
      <circle cx="321" cy="28" r="26" fill="none" stroke="var(--white)" stroke-width="1.2"/>
    </svg>
  </section>
</main>
</body>
</html>
```